Website for Vornelix Capital, my new firm that raises money from investors to buy, build, own an...

Vornelix Capital needs a website! We are a new company with very experienced people, who invest in, own and build hotel properties, as well as apartments and other commercial real estate. We seek investors for our projects, and we provide safe, secure returns on their investment in our projects. Our new logo is designed to exhibit strength, class and security, and would like our website to continue on this theme. Our name, Vornelix, is a word-play on a Greek word “aristeia”, which means “excellence” and “a warriors finest moment of glory in war”. If you are in business, you realize that much of it is like war, with strategy and moves and opponents and competitors, and ever-changing economic conditions and threats that make business very much like war. We like to think that we are good at business (war), and so have named our company “Vornelix”, using the founders last name and the word “aristeia” combined. Another definition of "aristeia" is "performing at the peak of one's potential after a long struggle"...again, much like business in real life! The website design should exhibit financial security, smart moves, and positive growth towards a bright future.

Target Market(s)

The target market is smart and wealthy investors, with others such as brokers, cities and government agencies, lenders, sellers, partners, etc also looking at it.

Industry/Entity Type

Investment

Number of Pages Required

5+ page

Font styles to use
Sans Serif

Colors
fec214

Requirements
Must have
• Our website should have a landing page, a "about" or bio page, a projects page and a contact us page. Our new logo uses the colors black and gold, so this should be factored in to our site. The site should be simple, yet impactful and impressive. I have actually two logos, which can be mixed and interchanged in a complimentary way, each with their own unique look.
Nice to have
• I have uploaded a couple screenshots of a website i like, and the simplicity I mention.
Should not have
• The site should not be flashy or complicated or complex or "busy"

```html
<!DOCTYPE html>
<html lang="en">
<head>
<meta charset="utf-8">
<title>Vornelix Capital</title>
<link rel="stylesheet" href="https://fonts.googleapis.com/css2?family=Lato:wght@400;700;900&family=Poppins:wght@300;400&family=Open+Sans:wght@400;600;700&display=swap">
<style>
:root{
  --gold:#fec214;
  --gold-deep:#e8b417;
  --black:#000;
  --ink:#111;
  --grey-bg:#f4f4f4;
  --text-muted:#8c8c8c;
  --faint:#efefef;
  --white:#fff;
}
*{margin:0;padding:0;box-sizing:border-box}
html,body{width:1200px;height:2429px;overflow:hidden;background:var(--white)}
body{position:relative;font-family:"Open Sans",sans-serif;color:var(--ink)}
.abs{position:absolute}

/* header */
.topbar{left:0;top:0;width:1200px;height:52px;background:var(--black)}
.nav-home{left:618px;top:0;width:83px;height:68px}
.nav-link{top:0;height:52px;line-height:52px;font-size:15px;color:var(--gold);text-transform:uppercase;transform:translateX(-50%)}
.nav-link.is-active{color:var(--ink);top:4px}
.brand-name{left:80px;top:0;height:52px;line-height:52px;font-family:"Lato",sans-serif;font-weight:700;font-size:20px;color:var(--gold);letter-spacing:1px;white-space:nowrap}

/* hero */
.hero{left:0;top:52px;width:1200px;height:573px;
  background:linear-gradient(90deg,#5c5a78 0%,#8d7f98 14%,#b9b6c8 30%,#dfe0e8 48%,#f3f4f7 65%,#fafafb 100%)}
.hero-title{right:80px;top:212px;font-family:"Lato",sans-serif;font-weight:900;font-size:58px;line-height:66px;color:var(--ink);white-space:nowrap}
.hero-text{right:80px;top:294px;width:528px;text-align:right;font-family:"Poppins",sans-serif;font-weight:300;font-size:16.5px;line-height:22.5px;color:#6d6d6d}
.hero-btn{left:894px;top:380px;width:226px;height:49px;background:var(--gold);border-bottom:4px solid #a77d00;border-right:3px solid #c29200;font-family:"Poppins",sans-serif;font-size:16.5px;line-height:46px;text-align:center;color:var(--ink);text-transform:uppercase}

/* projects */
.projects-watermark{left:0;width:1200px;top:672px;text-align:center;font-family:"Lato",sans-serif;font-weight:900;font-size:151px;line-height:170px;color:var(--faint);letter-spacing:2px}
.project-feature{left:76px;top:784px;width:521px;height:521px;background:linear-gradient(180deg,#3f79c4 0%,#78a9d9 40%,#c9c7bb 62%,#6f7a6a 80%,#1a1a1a 100%)}
.project-caption{left:102px;top:1225px;font-family:"Lato",sans-serif;font-weight:700;font-size:40px;color:var(--white)}
.project-thumb-back{left:675px;top:889px;width:308px;height:308px;background:linear-gradient(180deg,#dfe3ea 0%,#a8a19a 45%,#7a8a6a 70%,#9b9a92 100%)}
.project-thumb-front{left:814px;top:999px;width:308px;height:306px;background:linear-gradient(180deg,#2f6fd8 0%,#5d8fe0 35%,#6b4a35 60%,#3b3a38 85%,#555 100%)}
.arrow{font-family:"Lato",sans-serif;font-weight:900;font-size:40px;line-height:40px}
.arrow-next{left:1036px;top:932px;color:var(--black)}
.arrow-prev{left:733px;top:1234px;color:var(--gold-deep)}

/* about */
.about-band{left:0;top:1381px;width:1200px;height:322px;background:var(--grey-bg)}
.about-title{left:0;width:1200px;top:1438px;text-align:center;font-family:"Lato",sans-serif;font-weight:900;font-size:39px;color:var(--ink)}
.about-text{left:155px;top:1495px;width:890px;text-align:center;font-size:14px;line-height:20.5px;color:var(--text-muted)}
.service-icon{top:1632px;width:142px;height:142px}
.service-title{top:1786px;width:360px;text-align:center;font-family:"Lato",sans-serif;font-weight:700;font-size:22.5px;color:var(--ink)}
.service-text{top:1822px;width:300px;text-align:center;font-size:14.3px;line-height:21px;color:var(--text-muted)}

/* contact */
.contact-band{left:0;top:1927px;width:1200px;height:440px;background:linear-gradient(100deg,#3a2a2a 0%,#2a2224 35%,#1f1a1c 65%,#3b2c25 100%)}
.contact-panel{left:340px;top:1991px;width:520px;height:311px;background:rgba(130,130,130,.35)}
.contact-title{left:340px;width:520px;top:2016px;text-align:center;font-family:"Lato",sans-serif;font-weight:900;font-size:39px;color:var(--white)}
.contact-icon{width:52px;height:52px}
.contact-phone{left:448px;top:2098px;font-weight:700;font-size:16.5px;color:var(--white)}
.contact-email{left:644px;top:2098px;font-size:16.5px;color:#d0d0d0}
.contact-address{left:448px;top:2160px;width:380px;font-size:14.5px;line-height:21px;color:#cfcfcf}
.social{top:2229px;width:42px;height:42px;border-radius:50%}
.social-filled{background:#8a8a8a}
.social-outline{border:1.5px solid #a9a9a9}

/* footer */
.footer{left:0;top:2367px;width:1200px;height:62px;background:var(--black);text-align:center;line-height:62px;font-size:14.5px;color:var(--white)}
.footer strong{color:var(--gold);font-weight:700}
</style>
</head>
<body>

<!-- header -->
<div class="abs topbar"></div>
<div class="abs brand-name">VORNELIX CAPITAL</div>
<svg class="abs nav-home" viewBox="0 0 83 68"><path d="M0 0H83V52L41.5 68 0 52Z" fill="#fff"/></svg>
<div class="abs nav-link is-active" style="left:659px">Home</div>
<div class="abs nav-link" style="left:787px">About Us</div>
<div class="abs nav-link" style="left:926px">Project</div>
<div class="abs nav-link" style="left:1075px">Contact Us</div>

<!-- hero -->
<div class="abs hero" role="img" aria-label="Double-exposure photo of a businessman's profile blended with a city skyline"></div>
<h1 class="abs hero-title">VORNELIX CAPITAL</h1>
<p class="abs hero-text">Vornelix Capital are a new company with very experienced people, who invest in, own and build hotel properties, as well as apartments and other commercial real estate.</p>
<div class="abs hero-btn">Get Started Now</div>

<!-- projects -->
<div class="abs projects-watermark">PROJECTS</div>
<div class="abs project-feature" role="img" aria-label="Rendering of a modern high-rise residential complex under a blue sky"></div>
<div class="abs project-caption">Project's Name</div>
<div class="abs project-thumb-back" role="img" aria-label="Photo of a row of colourful terraced houses on a cobbled street"></div>
<div class="abs project-thumb-front" role="img" aria-label="Photo of a modern brick and glass office building"></div>
<div class="abs arrow arrow-next">»</div>
<div class="abs arrow arrow-prev">«</div>

<!-- about -->
<div class="abs about-band"></div>
<h2 class="abs about-title">ABOUT US</h2>
<p class="abs about-text">Lorem Ipsum is simply dummy text of the printing and typesetting industry. Lorem Ipsum has been the industry's standard dummy text ever since the 1500s, when an unknown printer took a galley of type and scrambled it to make a type specimen book.Lorem Ipsum is simply dummy text of the printing and typesetting industry. Lorem Ipsum has been the industry's standard dummy text ever since the 1500s, when an unknown printer took a galley of type and scrambled it to make a type specimen book.</p>

<svg class="abs service-icon" style="left:172px" viewBox="0 0 142 142">
  <circle cx="71" cy="71" r="71" fill="#fff"/><circle cx="71" cy="71" r="60" fill="#e8b417"/>
  <g fill="#c99608"><rect x="52" y="40" width="38" height="62"/><rect x="44" y="98" width="54" height="4"/></g>
  <g fill="#e8b417"><rect x="58" y="48" width="6" height="6"/><rect x="68" y="48" width="6" height="6"/><rect x="78" y="48" width="6" height="6"/><rect x="58" y="60" width="6" height="6"/><rect x="68" y="60" width="6" height="6"/><rect x="78" y="60" width="6" height="6"/><rect x="58" y="72" width="6" height="6"/><rect x="68" y="72" width="6" height="6"/><rect x="78" y="72" width="6" height="6"/><rect x="66" y="86" width="10" height="12"/></g>
</svg>
<svg class="abs service-icon" style="left:528px" viewBox="0 0 142 142">
  <circle cx="71" cy="71" r="71" fill="#fff"/><circle cx="71" cy="71" r="60" fill="#e8b417"/>
  <g fill="#c99608"><rect x="40" y="44" width="26" height="58"/><rect x="66" y="58" width="36" height="44"/></g>
  <g fill="#e8b417"><rect x="46" y="52" width="5" height="6"/><rect x="55" y="52" width="5" height="6"/><rect x="46" y="64" width="5" height="6"/><rect x="55" y="64" width="5" height="6"/><rect x="46" y="76" width="5" height="6"/><rect x="55" y="76" width="5" height="6"/><rect x="72" y="66" width="6" height="6"/><rect x="82" y="66" width="6" height="6"/><rect x="92" y="66" width="5" height="6"/><rect x="72" y="78" width="6" height="6"/><rect x="82" y="78" width="6" height="6"/><rect x="92" y="78" width="5" height="6"/></g>
</svg>
<svg class="abs service-icon" style="left:884px" viewBox="0 0 142 142">
  <circle cx="71" cy="71" r="71" fill="#fff"/><circle cx="71" cy="71" r="60" fill="#e8b417"/>
  <g fill="#d4a20c"><rect x="38" y="62" width="20" height="40"/><rect x="58" y="48" width="26" height="54"/><rect x="84" y="68" width="22" height="34"/></g>
  <g fill="#e8b417"><rect x="63" y="56" width="16" height="3"/><rect x="63" y="64" width="16" height="3"/><rect x="63" y="72" width="16" height="3"/><rect x="63" y="80" width="16" height="3"/><rect x="42" y="70" width="12" height="3"/><rect x="42" y="78" width="12" height="3"/><rect x="88" y="76" width="14" height="3"/><rect x="88" y="84" width="14" height="3"/></g>
</svg>

<h3 class="abs service-title" style="left:63px">Hotel Property</h3>
<h3 class="abs service-title" style="left:419px">Apartments</h3>
<h3 class="abs service-title" style="left:775px">Commercial Real Estate</h3>
<p class="abs service-text" style="left:93px">Lorem Ipsum is simply dummy text of the printing and typesetting industry.</p>
<p class="abs service-text" style="left:449px">Lorem Ipsum is simply dummy text of the printing and typesetting industry.</p>
<p class="abs service-text" style="left:805px">Lorem Ipsum is simply dummy text of the printing and typesetting industry.</p>

<!-- contact -->
<div class="abs contact-band" role="img" aria-label="Dim photo of a house porch with a white railing overlooking mountains at dusk"></div>
<div class="abs contact-panel"></div>
<h2 class="abs contact-title">KEEP IN TOUCH</h2>

<svg class="abs contact-icon" style="left:380px;top:2084px" viewBox="0 0 52 52"><circle cx="26" cy="26" r="26" fill="#fff"/><path d="M20 17l4 5-2.5 2.5a14 14 0 0 0 6 6L30 28l5 4-2 3c-8 0-16-8-16-16z" fill="none" stroke="#222" stroke-width="1.8" stroke-linejoin="round"/></svg>
<div class="abs contact-phone">123 456 7878</div>
<svg class="abs contact-icon" style="left:578px;top:2084px" viewBox="0 0 52 52"><circle cx="26" cy="26" r="26" fill="#fff"/><rect x="17" y="19" width="18" height="14" rx="2" fill="none" stroke="#222" stroke-width="1.8"/><path d="M17 21l9 6 9-6" fill="none" stroke="#222" stroke-width="1.8"/></svg>
<div class="abs contact-email">info@vornelix.com</div>
<svg class="abs contact-icon" style="left:380px;top:2156px" viewBox="0 0 52 52"><circle cx="26" cy="26" r="26" fill="#fff"/><path d="M26 37s-8-8-8-14a8 8 0 0 1 16 0c0 6-8 14-8 14z" fill="none" stroke="#222" stroke-width="1.8"/><circle cx="26" cy="23" r="2.8" fill="none" stroke="#222" stroke-width="1.6"/></svg>
<p class="abs contact-address">123, Lorem Ipsum is simply dummy text of the printing and typesetting industry.</p>

<div class="abs social social-filled" style="left:526px"></div>
<div class="abs social social-outline" style="left:578px"></div>
<div class="abs social social-outline" style="left:630px"></div>

<!-- footer -->
<div class="abs footer">© <strong>2018 VORNELIX CAPITAL</strong> ~ All rights reserved.</div>

</body>
</html>
```